Awesome Digital Ad Design – Vexora Adloop

I am going to be setting up a Vexora Adloop ad campaign I need creatives for.

Several sizes are needed in the end, however, please submit your design concept in the following 2 sizes to start:
Medium rectangle: 300X250
Leaderboard: 728X90

Original artwork/design files and images used expected upon payment and as part of the final delivery.

Ads should match our company brand and the information on this webpage: http://www.harbelstandwork.com/real-estate-marketing/
SEE MORE INSTRUCTIONS IN ATTACHED WORD DOC

Target Market(s)

Business-To-Business Audience –Real Estate Company Executives (Presidents/VPs/Owners/CEOs/Sales Managers).

Industry/Entity Type

Real Estate

Font styles to use
Sans Serif

Requirements
Must have
• Copy should be minimal words, billboard like. Please use real photos/images that would appeal to real estate high-level decision-maker executives.
Should not have
• No cartoons or graphics

```html
<!DOCTYPE html>
<html lang="en">
<head>
<meta charset="utf-8">
<title>Client Follow-Up Made Simple – Harbel Standwork Leaderboard</title>
<link href="https://fonts.googleapis.com/css2?family=Oswald:wght@500;600;700&family=Roboto:wght@500;700&display=swap" rel="stylesheet">
<style>
  :root {
    --navy-deep: #0f1f3c;
    --navy: #1c3562;
    --navy-light: #34527f;
    --white: #ffffff;
    --gold: #efd78e;
    --ink: #1d2a44;
    --orange-top: #ff8a2a;
    --orange-bottom: #e85a0c;
    --band-steel: #7d95ad;
    --band-maroon: #7b2c3e;
    --band-tan: #cdbd8e;
    --band-slate: #5b7592;
    --suit: #1b2233;
    --shirt: #c9d2de;
  }
  * { margin: 0; padding: 0; box-sizing: border-box; }
  html, body { width: 1200px; height: 148px; overflow: hidden; background: var(--white); }
  .leaderboard {
    position: relative;
    width: 1200px;
    height: 148px;
    overflow: hidden;
    background:
      linear-gradient(115deg, transparent 40%, rgba(120,160,220,0.16) 48%, transparent 56%),
      linear-gradient(100deg, var(--navy-deep) 0%, var(--navy) 45%, var(--navy-light) 100%);
    font-family: "Roboto", Arial, sans-serif;
  }
  .executive-photo {
    position: absolute;
    left: 640px; top: 0;
    width: 560px; height: 132px;
    background:
      radial-gradient(ellipse 40px 70px at 85px 72px, rgba(150,205,255,0.45), rgba(150,205,255,0) 100%),
      radial-gradient(ellipse 150px 110px at 290px 90px, rgba(27,34,51,0.95), rgba(27,34,51,0) 100%),
      linear-gradient(90deg, rgba(28,53,98,0) 0%, #26385a 18%, #2a3550 45%, #38465f 65%, #7e8aa0 82%, #dfe4eb 100%);
  }
  .brand-panel {
    position: absolute;
    left: 0; top: 0;
    width: 230px; height: 132px;
  }
  .brand-name {
    position: absolute;
    left: 28px; top: 48px;
    width: 150px;
    font-weight: 700;
    font-size: 17px;
    line-height: 1.2;
    color: var(--ink);
  }
  .headline {
    position: absolute;
    left: 220px; top: 9px;
    width: 440px;
    text-align: center;
    color: var(--white);
  }
  .headline-top {
    font-family: "Oswald", "Arial Narrow", sans-serif;
    font-weight: 600;
    font-size: 38px;
    line-height: 40px;
    letter-spacing: 2.5px;
  }
  .headline-main {
    font-family: "Oswald", "Arial Narrow", sans-serif;
    font-weight: 700;
    font-size: 50px;
    line-height: 52px;
    letter-spacing: 3px;
    color: var(--gold);
  }
  .tagline {
    font-weight: 500;
    font-size: 24px;
    line-height: 28px;
  }
  .cta-button {
    position: absolute;
    left: 978px; top: 40px;
    width: 194px; height: 58px;
    border-radius: 4px;
    background: linear-gradient(180deg, var(--orange-top), var(--orange-bottom));
    color: var(--white);
    font-weight: 700;
    font-size: 23px;
    display: flex; align-items: center; justify-content: center;
    box-shadow: 0 2px 4px rgba(0,0,0,0.35);
  }
  .color-band {
    position: absolute;
    left: 0; bottom: 0;
    width: 1200px; height: 16px;
    display: flex; gap: 2px;
    background: var(--white);
  }
  .color-band span { flex: 1; }
  .steel { background: var(--band-steel); }
  .maroon { background: var(--band-maroon); }
  .tan { background: var(--band-tan); }
  .slate { background: var(--band-slate); }
</style>
</head>
<body>
  <div class="leaderboard">
    <div class="executive-photo" role="img" aria-label="Photo of a businessman in a dark suit writing with a pen, beside a glowing silhouette of a walking man"></div>

    <svg class="brand-panel" viewBox="0 0 230 132" aria-hidden="true">
      <polygon points="0,0 198,0 228,66 198,132 0,132" fill="#dfe6ee"/>
      <polygon points="0,0 192,0 220,66 192,132 0,132" fill="#ffffff"/>
    </svg>
    <div class="brand-name">Harbel Standwork</div>

    <div class="headline">
      <div class="headline-top">CLIENT FOLLOW-UP</div>
      <div class="headline-main">MADE SIMPLE</div>
      <div class="tagline">Virtually No Cost To Your Company!</div>
    </div>

    <div class="cta-button">LEARN MORE</div>

    <div class="color-band">
      <span class="steel"></span><span class="maroon"></span><span class="tan"></span>
      <span class="slate"></span><span class="steel"></span><span class="maroon"></span>
      <span class="tan"></span><span class="steel"></span><span class="slate"></span>
      <span class="maroon"></span><span class="tan"></span><span class="steel"></span>
      <span class="maroon"></span><span class="slate"></span>
    </div>
  </div>
</body>
</html>
```